Presentation Of Our Epidemiology Consulting Framework

We need a slide deck (png files) for PowerPoint that describes our organization and type of clients we serve, and our 6 phase framework that explains how we work with clients. Please use the minimum amount of text on each slide.  We want a more visual display of how to work with us. We want it to look very similar to our brochure.  We want to also have a few extra branded slides without text that can be used as a template if we decide to add to the deck later or create a new slide deck.
Colors
#56588C
#F28444
#F2E088
#F24C27
#ODODOD

```html
<!DOCTYPE html>
<html lang="en">
<head>
<meta charset="utf-8">
<title>Kestrel Health – Framework Deck</title>
<link href="https://fonts.googleapis.com/css2?family=Roboto:wght@400;500;700&display=swap" rel="stylesheet">
<style>
:root{
  --canvas:#a7a7a7;
  --navy-1:#221a62;
  --navy-2:#34288a;
  --violet:#56588C;
  --violet-light:#6b62c9;
  --orange:#F28444;
  --orange-deep:#F24C27;
  --white:#ffffff;
  --ink:#0D0D0D;
}
*{box-sizing:border-box;margin:0;padding:0}
html,body{width:1012px;height:1200px;overflow:hidden}
body{background:var(--canvas);font-family:"Roboto",Arial,sans-serif;color:var(--white);position:relative}
.slide{position:absolute;width:460px;height:258px;overflow:hidden;
  background:radial-gradient(ellipse at 70% 60%,var(--navy-2),var(--navy-1) 75%)}
.col-a{left:32px}.col-b{left:521px}
.row-1{top:38px}.row-2{top:326px}.row-3{top:616px}.row-4{top:904px}
.abs{position:absolute}
.brand{position:absolute;left:31px;top:11px;display:flex;align-items:center;gap:5px;font-weight:500;font-size:15px;color:var(--white)}
.brand .dot{width:11px;height:11px;border-radius:50%;background:var(--orange)}
.slide-title{position:absolute;right:31px;top:15px;font-size:12px;font-weight:700}
.subtitle{position:absolute;left:0;right:0;text-align:center;font-size:9px;font-weight:700}
.footer{position:absolute;left:31px;right:31px;bottom:0;height:22px;border-radius:11px 11px 0 0;
  background:linear-gradient(90deg,var(--orange-deep),var(--orange) 70%,#f5a35f);
  font-size:4.6px;font-weight:500;text-align:center;line-height:24px}
.page-no{position:absolute;right:13px;bottom:9px;font-size:4.6px;font-weight:500}
.photo{position:relative;overflow:hidden}
.photo::after{content:"";position:absolute;inset:0;background:linear-gradient(180deg,rgba(255,255,255,.08),rgba(0,0,0,.18))}
.tone-clinic{background:linear-gradient(135deg,#e9e4de 0%,#c9c2bb 45%,#6d6a72 100%)}
.tone-office{background:linear-gradient(135deg,#3c3f4a 0%,#8b857d 55%,#d8cfc3 100%)}
.tone-warm{background:linear-gradient(135deg,#e6d3bc 0%,#b08f74 50%,#4a4a5c 100%)}
.tone-blue{background:linear-gradient(135deg,#27356b 0%,#5073a6 50%,#c9a999 100%)}
.tone-bright{background:linear-gradient(135deg,#f1efe9 0%,#d5cdc2 50%,#e7783f 100%)}
.btn{position:absolute;height:22px;border-radius:11px;background:linear-gradient(90deg,var(--orange-deep),var(--orange));
  display:flex;align-items:center;justify-content:center;gap:5px;font-size:7px;font-weight:500;box-shadow:0 2px 3px rgba(0,0,0,.3)}
.btn svg{width:7px;height:6px}
.cover-headline{left:34px;top:68px;font-size:12px;font-weight:700;line-height:14.5px}
.cover-headline .accent{color:var(--orange)}
.cover-body{left:34px;width:193px;font-size:4.6px;line-height:7.2px;text-align:justify}
.cover-label{left:34px;top:162px;font-size:7px;font-weight:500}
.step{position:absolute;left:246px;display:flex;align-items:center;gap:9px;font-size:7px;line-height:12px;width:190px}
.step .num{flex:none;width:22px;height:22px;border-radius:50%;background:radial-gradient(circle at 40% 35%,var(--orange),var(--orange-deep));
  font-size:5.5px;font-weight:700;display:flex;align-items:center;justify-content:center}
.phase{position:absolute;width:70px;text-align:center;font-size:5.5px;font-weight:700;line-height:8px}
.phase .ring{width:42px;height:42px;margin:0 auto 4px;border-radius:50%;background:var(--white);border:2px solid var(--orange);display:flex;align-items:center;justify-content:center}
.phase .ring svg{width:24px;height:24px}
.pill{position:absolute;width:72px;height:180px;border-radius:36px;background:rgba(20,14,70,.4)}
.card{position:absolute;top:90px;width:93px;height:99px;background:var(--white);padding:4px;color:var(--ink);text-align:center;font-size:5.5px;font-weight:700;line-height:8px}
.card .photo{height:67px;margin-bottom:5px}
.bullet{position:absolute;left:71px;display:flex;align-items:center;gap:8px;font-size:7px;font-weight:500}
.bullet i{width:7px;height:7px;border-radius:50%;background:var(--orange);display:block;box-shadow:2px 0 0 var(--violet-light)}
.deliver{position:absolute;display:flex;align-items:center;gap:5px;font-size:7px;font-weight:700;line-height:9.5px}
.deliver.left{right:312px;text-align:right}
.deliver.right{left:305px}
.diamond{flex:none;width:26px;height:26px;display:flex;align-items:center;justify-content:center}
.diamond>span{width:19px;height:19px;border-radius:4px;background:var(--white);transform:rotate(45deg);display:flex;align-items:center;justify-content:center}
.diamond svg{width:12px;height:12px;transform:rotate(-45deg)}
.tile{position:absolute;top:71px;width:93px;text-align:center;font-size:5.5px;font-weight:700;line-height:8px}
.tile .photo{height:111px;margin-bottom:5px}
.hero-mark{position:absolute;width:150px;height:150px}
.close-brand{left:0;right:0;top:54px;justify-content:center;font-size:22px}
.close-brand .dot{width:16px;height:16px}
.close-head{left:0;right:0;top:93px;text-align:center;font-size:11.5px;font-weight:700;line-height:14px}
.close-body{left:100px;right:100px;top:124px;text-align:center;font-size:8px;line-height:14px}
</style>
</head>
<body>
<svg width="0" height="0" style="position:absolute">
  <defs>
    <g id="i-team" fill="none" stroke="#F28444" stroke-width="1.4"><circle cx="12" cy="7" r="3"/><circle cx="5.5" cy="10" r="2.2"/><circle cx="18.5" cy="10" r="2.2"/><path d="M6.5 20v-3a5.5 5.5 0 0 1 11 0v3M1.5 20v-2a4 4 0 0 1 4-4M22.5 20v-2a4 4 0 0 0-4-4"/></g>
    <g id="i-flow" fill="none" stroke="#F28444" stroke-width="1.4"><circle cx="12" cy="12" r="4"/><path d="M12 5v3M12 16v3M5 12h3M16 12h3"/><rect x="2" y="2" width="6" height="4"/><rect x="16" y="18" width="6" height="4"/></g>
    <g id="i-data" fill="none" stroke="#F28444" stroke-width="1.4"><ellipse cx="10" cy="5" rx="7" ry="2.5"/><path d="M3 5v11c0 1.4 3.1 2.5 7 2.5M17 5v5M3 10.5c0 1.4 3.1 2.5 7 2.5"/><circle cx="18" cy="17" r="3.5"/><path d="M18 12v1.5M18 20.5V22M13 17h1.5M21.5 17H23"/></g>
    <g id="i-chart" fill="none" stroke="#F28444" stroke-width="1.4"><path d="M2 21h20"/><rect x="4" y="14" width="3" height="7"/><rect x="10" y="10" width="3" height="11"/><rect x="16" y="6" width="3" height="15"/><path d="M3 12l6-5 4 3 8-7"/></g>
    <g id="i-target" fill="none" stroke="#F28444" stroke-width="1.4"><circle cx="11" cy="13" r="8"/><circle cx="11" cy="13" r="4.5"/><circle cx="11" cy="13" r="1.2" fill="#F28444"/><path d="M11 13l9-9M17 4h3v3"/></g>
    <g id="i-present" fill="none" stroke="#F28444" stroke-width="2"><rect x="4" y="3" width="16" height="11"/><path d="M12 14v6M8 20h8M7 11l4-4 3 3 3-3"/></g>
    <g id="i-cycle" fill="none" stroke="#F28444" stroke-width="2"><path d="M5 12a7 7 0 0 1 12-5l2 2M19 12a7 7 0 0 1-12 5l-2-2"/><path d="M19 4v5h-5M5 20v-5h5"/></g>
    <g id="i-support" fill="none" stroke="#F28444" stroke-width="2"><path d="M4 14v-2a8 8 0 0 1 16 0v2"/><rect x="2" y="13" width="4" height="6" rx="1"/><rect x="18" y="13" width="4" height="6" rx="1"/><path d="M20 19q0 3-5 3"/></g>
    <g id="i-tree" fill="none" stroke="#F28444" stroke-width="2"><rect x="9" y="2" width="6" height="5"/><rect x="2" y="17" width="6" height="5"/><rect x="16" y="17" width="6" height="5"/><path d="M12 7v5M5 17v-5h14v5"/></g>
    <g id="i-mail"><rect x="0.5" y="0.5" width="13" height="10" rx="1" fill="#fff"/><path d="M1 1l6 5 6-5" fill="none" stroke="#F24C27" stroke-width="1.2"/></g>
  </defs>
</svg>

<!-- Cover -->
<section class="slide col-a row-1">
  <svg class="abs" style="left:0;top:0" width="460" height="258" viewBox="0 0 460 258">
    <circle cx="390" cy="65" r="166" fill="none" stroke="#ffffff" stroke-width="0.8"/>
    <circle cx="390" cy="65" r="150" fill="none" stroke="var(--orange)" stroke-width="1.2"/>
    <circle cx="390" cy="65" r="132" fill="#2b2173"/>
    <circle cx="390" cy="238" r="40" fill="var(--orange)"/>
    <circle cx="390" cy="238" r="31" fill="#ffffff"/>
  </svg>
  <div class="abs photo tone-clinic" role="img" aria-label="Photo of two doctors reviewing results together" style="left:280px;top:-47px;width:224px;height:224px;border-radius:50%"></div>
  <div class="brand" style="top:18px;font-size:20px"><span class="dot" style="width:15px;height:15px"></span>Kestrel Health</div>
  <h1 class="abs cover-headline">Transforming Health Data into<br>Community Impact:<br><span class="accent">The Kestrel Health Framework</span></h1>
  <p class="abs cover-body" style="top:116px">Kestrel Health LLC is an epidemiology consulting firm that supports large nonprofit organizations and government agencies that serve black, indigenous, and people of color commonly referred to as BIPOC communities. Our diverse team of innovative global public health professionals are ready to serve your organization by helping you address your most pressing challenges.</p>
  <h2 class="abs cover-label">Our Approach</h2>
  <p class="abs cover-body" style="top:173px">At Kestrel Health LLC, we believe in transforming health data into actionable insights for BIPOC communities. Our proven six-phase partnership model ensures your organization's success in communicating vital health information effectively.</p>
  <div class="btn" style="left:0;top:204px;width:170px;border-radius:0 11px 11px 0"><svg viewBox="0 0 14 11"><use href="#i-mail"/></svg>Email : hello@kestrelhealth.example</div>
</section>

<!-- Collaborative Refinement -->
<section class="slide col-b row-1">
  <div class="brand"><span class="dot"></span>Kestrel Health</div>
  <h2 class="slide-title">Collaborative Refinement</h2>
  <h3 class="subtitle" style="left:184px;right:auto;top:49px">Ensuring Perfect Alignment</h3>
  <div class="bullet" style="top:103px"><i></i>Presentation of initial frameworks</div>
  <div class="bullet" style="top:124px"><i></i>Interactive feedback sessions</div>
  <div class="bullet" style="top:146px"><i></i>Draft review and optimization</div>
  <div class="bullet" style="top:167px"><i></i>Stakeholder input integration</div>
  <svg class="hero-mark" style="left:250px;top:72px" viewBox="0 0 150 150">
    <circle cx="75" cy="75" r="70" fill="none" stroke="#56588C" stroke-width="10"/>
    <path d="M75 5a70 70 0 0 1 70 70" fill="none" stroke="#F28444" stroke-width="10" stroke-linecap="round"/>
    <path d="M5 75a70 70 0 0 0 70 70" fill="none" stroke="#F24C27" stroke-width="10" stroke-linecap="round"/>
    <circle cx="75" cy="75" r="50" fill="#2d2380"/>
    <g transform="translate(51 51) scale(2)"><use href="#i-cycle"/></g>
  </svg>
  <div class="footer">© Copyrights 2025 | All Rights Reserved</div>
  <div class="page-no">05</div>
</section>

<!-- Discovery -->
<section class="slide col-a row-2">
  <div class="brand"><span class="dot"></span>Kestrel Health</div>
  <h2 class="slide-title">Discovery &amp; Vision Alignment</h2>
  <svg class="abs" style="left:0;top:0" width="240" height="258" viewBox="0 0 240 258">
    <circle cx="120" cy="130" r="86" fill="none" stroke="#ffffff" stroke-width="0.8"/>
    <circle cx="120" cy="130" r="75" fill="none" stroke="var(--orange)" stroke-width="1.4"/>
  </svg>
  <div class="abs photo tone-office" role="img" aria-label="Photo of a health professional working on a laptop" style="left:54px;top:64px;width:132px;height:132px;border-radius:50%"></div>
  <h3 class="subtitle" style="left:243px;text-align:left;top:59px">Building the Foundation for Success</h3>
  <div class="step" style="top:90px"><span class="num">01</span>Deep-dive exploration of your organization's unique challenges and opportunities</div>
  <div class="step" style="top:120px"><span class="num">01</span>Strategic alignment of goals and expectations</div>
  <div class="step" style="top:144px"><span class="num">01</span>Custom-tailored solution design</div>
  <div class="step" style="top:174px"><span class="num">01</span>Clear roadmap development with defined milestones</div>
  <div class="footer">© Copyrights 2025 | All Rights Reserved</div>
  <div class="page-no">02</div>
</section>

<!-- Impact Delivery -->
<section class="slide col-b row-2">
  <div class="brand"><span class="dot"></span>Kestrel Health</div>
  <h2 class="slide-title">Impact Delivery</h2>
  <h3 class="subtitle" style="top:52px">Bringing Vision to Reality</h3>
  <svg class="hero-mark" style="left:155px;top:78px" viewBox="0 0 150 150">
    <circle cx="75" cy="75" r="64" fill="none" stroke="#56588C" stroke-width="10"/>
    <path d="M75 11a64 64 0 0 1 64 64" fill="none" stroke="#F28444" stroke-width="10" stroke-linecap="round"/>
    <path d="M11 75a64 64 0 0 0 64 64" fill="none" stroke="#F24C27" stroke-width="10" stroke-linecap="round"/>
    <circle cx="75" cy="75" r="45" fill="#2d2380"/>
    <g transform="translate(53 53) scale(1.8)"><use href="#i-chart"/></g>
  </svg>
  <div class="deliver left" style="top:85px">Final deliverable<br>presentation<span class="diamond"><span><svg viewBox="0 0 24 24"><use href="#i-present"/></svg></span></span></div>
  <div class="deliver left" style="top:147px">Implementation<br>support<span class="diamond"><span><svg viewBox="0 0 24 24"><use href="#i-support"/></svg></span></span></div>
  <div class="deliver right" style="top:85px"><span class="diamond"><span><svg viewBox="0 0 24 24"><use href="#i-cycle"/></svg></span></span>Knowledge transfer</div>
  <div class="deliver right" style="top:147px"><span class="diamond"><span><svg viewBox="0 0 24 24"><use href="#i-tree"/></svg></span></span>Impact measurement<br>framework</div>
  <div class="footer">© Copyrights 2025 | All Rights Reserved</div>
  <div class="page-no">06</div>
</section>

<!-- Partnership Launch -->
<section class="slide col-a row-3">
  <div class="brand"><span class="dot"></span>Kestrel Health</div>
  <h2 class="slide-title">Partnership Launch</h2>
  <h3 class="subtitle" style="top:51px">Setting the Stage for Excellence</h3>
  <div class="pill" style="left:32px;top:106px"></div>
  <div class="pill" style="left:113px;top:87px"></div>
  <div class="pill" style="left:276px;top:87px"></div>
  <div class="pill" style="left:357px;top:106px"></div>
  <svg class="abs" style="left:0;top:0" width="460" height="258" viewBox="0 0 460 258">
    <path d="M94 258A136 104 0 0 1 366 258" fill="var(--orange)"/>
  </svg>
  <div class="abs photo tone-warm" role="img" aria-label="Photo of a smiling team meeting around a table" style="left:97px;top:158px;width:266px;height:200px;border-radius:50% 50% 0 0 / 50% 50% 0 0"></div>
  <div class="phase" style="left:33px;top:118px"><div class="ring"><svg viewBox="0 0 24 24"><use href="#i-team"/></svg></div>Formation of<br>dedicated project<br>team</div>
  <div class="phase" style="left:114px;top:98px"><div class="ring"><svg viewBox="0 0 24 24"><use href="#i-flow"/></svg></div>Establishment of<br>collaborative<br>workflow</div>
  <div class="phase" style="left:195px;top:82px"><div class="ring"><svg viewBox="0 0 24 24"><use href="#i-data"/></svg></div>Comprehensive<br>data gathering</div>
  <div class="phase" style="left:277px;top:98px"><div class="ring"><svg viewBox="0 0 24 24"><use href="#i-chart"/></svg></div>Strategic timeline<br>planning</div>
  <div class="phase" style="left:358px;top:118px"><div class="ring"><svg viewBox="0 0 24 24"><use href="#i-target"/></svg></div>Stakeholder<br>engagement and<br>vision capture</div>
  <div class="footer">© Copyrights 2025 | All Rights Reserved</div>
  <div class="page-no">03</div>
</section>

<!-- Evolution & Growth -->
<section class="slide col-b row-3">
  <div class="brand"><span class="dot"></span>Kestrel Health</div>
  <h2 class="slide-title">Evolution &amp; Growth</h2>
  <h3 class="subtitle" style="top:51px">Sustaining Long-term Success</h3>
  <div class="tile" style="left:31px"><div class="photo tone-bright" role="img" aria-label="Photo of a woman smiling beside a sticky-note wall"></div>Project success<br>celebration</div>
  <div class="tile" style="left:132px"><div class="photo tone-office" role="img" aria-label="Photo of a man working at a laptop in an office"></div>Future opportunities<br>exploration</div>
  <div class="tile" style="left:233px"><div class="photo tone-blue" role="img" aria-label="Photo of colleagues shaking hands"></div>Partnership evolution<br>planning</div>
  <div class="tile" style="left:335px"><div class="photo tone-clinic" role="img" aria-label="Photo of two colleagues reviewing a tablet"></div>Continuous improvement<br>recommendations</div>
  <div class="footer">© Copyrights 2025 | All Rights Reserved</div>
  <div class="page-no">07</div>
</section>

<!-- Expert Execution -->
<section class="slide col-a row-4">
  <div class="brand"><span class="dot"></span>Kestrel Health</div>
  <h2 class="slide-title">Expert Execution</h2>
  <h3 class="subtitle" style="top:50px">Where Science Meets Service</h3>
  <p class="subtitle" style="top:64px;font-size:5.5px;font-weight:500">Our specialized team begins the transformation process:</p>
  <div class="card" style="left:31px"><div class="photo tone-blue" role="img" aria-label="Photo of a researcher taking notes at a laptop"></div>In-depth research and<br>analysis</div>
  <div class="card" style="left:133px"><div class="photo tone-clinic" role="img" aria-label="Photo of a team reviewing printed drafts"></div>Content development and<br>refinement</div>
  <div class="card" style="left:234px"><div class="photo tone-bright" role="img" aria-label="Photo of an analyst presenting at a whiteboard"></div>Data interpretation and<br>visualization</div>
  <div class="card" style="left:336px"><div class="photo tone-blue" role="img" aria-label="Photo of a woman on a video call"></div>Plain language translation<br>of complex health</div>
  <div class="footer">© Copyrights 2025 | All Rights Reserved</div>
  <div class="page-no">04</div>
</section>

<!-- Closing -->
<section class="slide col-b row-4">
  <svg class="abs" style="left:0;top:0" width="460" height="258" viewBox="0 0 460 258">
    <circle cx="230" cy="128" r="147" fill="rgba(40,30,110,.55)" stroke="var(--orange)" stroke-width="1.2"/>
  </svg>
  <div class="brand close-brand"><span class="dot"></span>Kestrel Health</div>
  <h2 class="abs close-head">Ready to Transform Your Health<br>Communication?</h2>
  <p class="abs close-body">Contact us to begin your journey toward more effective, equitable health communication.</p>
  <div class="btn" style="left:137px;top:154px;width:185px;height:23px"><svg viewBox="0 0 14 11"><use href="#i-mail"/></svg>Email : hello@kestrelhealth.example</div>
  <div class="footer">© Copyrights 2025 | All Rights Reserved</div>
  <div class="page-no">08</div>
</section>

</body>
</html>
```